TalkHarbor - Language Coaching Services

Sleek, innovative, trendy design for Language Coaching business.

TalkHarbor is a new UK based company that provides Language Coaching services. We offer highly personalized on-line and face to face language courses. We also impart learning techniques workshops based on the latest neuroscience research for second-language acquisition.

Target Market(s)

See attached info

Industry/Entity Type

Consulting

Contact Information for Business Card

TalkHarbor
DaniaKV@talkharbor.co.uk
TalkHarbor.co.uk
London, UK

Font styles to use
Sans Serif

```html
<!DOCTYPE html>
<html lang="en">
<head>
<meta charset="utf-8">
<title>TalkHarbor – Business Card</title>
<link rel="stylesheet" href="https://fonts.googleapis.com/css2?family=Exo+2:wght@400;500;600;700&display=swap">
<style>
  :root {
    --canvas-bg: #e6e8ea;
    --card-white: #ffffff;
    --brand-blue: #0f8fc4;
    --brand-blue-deep: #0a76b3;
    --brand-blue-light: #12a9d6;
    --ink: #1e1e1e;
    --on-blue: #ffffff;
  }
  * { box-sizing: border-box; margin: 0; padding: 0; }
  html, body {
    width: 1200px; height: 900px; overflow: hidden;
    background: var(--canvas-bg);
    font-family: "Exo 2", "Helvetica Neue", Arial, sans-serif;
  }
  .canvas {
    position: relative; width: 1200px; height: 900px;
    display: flex; justify-content: center; align-items: center; gap: 70px;
  }
  .card {
    position: relative; width: 340px; height: 600px;
    box-shadow: 0 14px 30px rgba(0,0,0,0.18);
  }
  /* Front */
  .card--front {
    background: var(--card-white);
    padding: 44px 34px 0;
    display: flex; flex-direction: column; align-items: center;
  }
  .front__wordmark {
    align-self: flex-start;
    font-size: 30px; line-height: 36px; font-weight: 600; letter-spacing: 1px;
    color: var(--brand-blue); text-transform: uppercase;
  }
  .front__emblem { margin-top: 20px; width: 210px; height: 210px; flex-shrink: 0; }
  .front__name {
    margin-top: 24px; font-size: 24px; line-height: 30px; font-weight: 700; color: var(--brand-blue);
  }
  .front__icons { margin-top: 10px; display: flex; gap: 14px; }
  .front__icons svg { width: 18px; height: 18px; fill: var(--brand-blue); }
  .front__contact {
    margin-top: 10px; text-align: center;
    font-size: 16px; line-height: 26px; color: var(--ink);
  }
  .front__address {
    margin-top: 2px; text-align: center;
    font-size: 16px; line-height: 24px; color: var(--brand-blue);
  }
  .front__rule {
    position: absolute; left: 34px; right: 34px; bottom: 26px;
    height: 2px; background: var(--brand-blue);
  }
  /* Back */
  .card--back {
    background: radial-gradient(circle at 45% 30%, var(--brand-blue-light), var(--brand-blue-deep) 80%);
    display: flex; flex-direction: column; align-items: center; justify-content: center;
    color: var(--on-blue);
  }
  .back__emblem { width: 130px; height: 130px; }
  .back__wordmark {
    margin-top: 22px; font-size: 36px; font-weight: 600; letter-spacing: 1px;
    text-transform: uppercase;
  }
  .back__url { margin-top: 4px; font-size: 16px; font-weight: 500; letter-spacing: 0.5px; }
</style>
</head>
<body>
<main class="canvas">
  <section class="card card--front" aria-label="Business card front">
    <div class="front__wordmark">TalkHarbor</div>
    <svg class="front__emblem" viewBox="0 0 230 230" aria-hidden="true">
      <circle cx="115" cy="115" r="104" fill="none" stroke="var(--brand-blue)" stroke-width="18"/>
    </svg>
    <div class="front__name">TalkHarbor</div>
    <div class="front__icons" aria-hidden="true">
      <svg viewBox="0 0 24 24"><path d="M6.6 10.8c1.4 2.8 3.8 5.1 6.6 6.6l2.2-2.2c.3-.3.7-.4 1-.2 1.1.4 2.3.6 3.6.6.6 0 1 .4 1 1V20c0 .6-.4 1-1 1C10.6 21 3 13.4 3 4c0-.6.4-1 1-1h3.5c.6 0 1 .4 1 1 0 1.3.2 2.5.6 3.6.1.3 0 .7-.2 1l-2.3 2.2z"/></svg>
      <svg viewBox="0 0 24 24"><path d="M2 5h20v14H2z"/><path d="M3 6.5 12 13.5 21 6.5" fill="none" stroke="#fff" stroke-width="1.5"/></svg>
      <svg viewBox="0 0 24 24"><circle cx="12" cy="12" r="10"/><path d="M2 12h20M12 2c3 3 3 17 0 20M12 2c-3 3-3 17 0 20M4 7h16M4 17h16" fill="none" stroke="#fff" stroke-width="1.2"/></svg>
      <svg viewBox="0 0 24 24"><path d="M12 2a7 7 0 0 0-7 7c0 5 7 13 7 13s7-8 7-13a7 7 0 0 0-7-7zm0 9.5A2.5 2.5 0 1 1 12 6.5a2.5 2.5 0 0 1 0 5z"/></svg>
    </div>
    <div class="front__contact">
      <div>+44 1632 960418</div>
      <div>DaniaKV@talkharbor.co.uk</div>
      <div>www.talkharbor.co.uk</div>
    </div>
    <div class="front__address">
      <div>27 Harbour Lane, TN33 4QR,</div>
      <div>London, UK</div>
    </div>
    <div class="front__rule"></div>
  </section>

  <section class="card card--back" aria-label="Business card back">
    <svg class="back__emblem" viewBox="0 0 130 130" aria-hidden="true">
      <circle cx="65" cy="65" r="58" fill="none" stroke="var(--on-blue)" stroke-width="9"/>
    </svg>
    <div class="back__wordmark">TalkHarbor</div>
    <div class="back__url">www.talkharbor.co.uk</div>
  </section>
</main>
</body>
</html>
```